Nivel Crest - Powerpoint Templates

We are a consultancy to help builders to optimize their planning in order to save building costs. For that reason we need templates for teasers and presentations where we offer our services, show our team and their capacities and present workflows, organization charts, price lists etc.

```html
<!DOCTYPE html>
<html lang="en">
<head>
<meta charset="utf-8">
<title>Nivel Crest – Presentation Templates</title>
<link rel="stylesheet" href="https://fonts.googleapis.com/css2?family=Orbitron:wght@600;700;800&family=Open+Sans:wght@400;600;700&display=swap">
<style>
:root{
  --page:#f7f5ee;
  --slide:#ffffff;
  --ink:#3a3a3e;
  --ink-dark:#2f2f33;
  --gray:#6e6e72;
  --text:#6b6b6b;
  --gold:#c38a34;
  --gold-light:#e9c25c;
  --line:#e4e4e4;
  --head:"Orbitron", sans-serif;
  --body:"Open Sans", sans-serif;
}
*{margin:0;padding:0;box-sizing:border-box}
html,body{width:1200px;height:4051px;overflow:hidden;background:var(--page);font-family:var(--body);color:var(--text)}
.slide{position:absolute;left:75px;width:1048px;height:588px;background:var(--slide);box-shadow:0 2px 10px rgba(0,0,0,.08);overflow:hidden}
.abs{position:absolute}
/* header */
.band{position:absolute;left:0;top:0}
.title{position:absolute;left:60px;top:42px;font-family:var(--head);font-weight:800;font-size:23px;letter-spacing:1.5px;color:var(--ink);text-transform:uppercase;word-spacing:8px;white-space:nowrap}
.title .accent{color:var(--gold)}
.logo{position:absolute;display:flex;align-items:center;gap:8px}
.logo-mark{width:22px;height:22px;border:3px solid var(--gold)}
.logo-name{font-family:var(--head);font-weight:700;font-size:16px;letter-spacing:1px;color:var(--ink);text-transform:uppercase;line-height:1}
.logo.light .logo-name{color:#fff}
/* teaser */
.teaser-title{left:60px;top:168px;font-family:var(--head);font-weight:800;font-size:40px;color:#fff;letter-spacing:2px}
.teaser-rule{left:60px;top:226px;width:120px;height:3px;background:var(--gold)}
.teaser-copy{left:60px;top:254px;width:340px;font-size:15.5px;line-height:28px;color:#f1f1f1;text-align:justify}
/* services */
.service{position:absolute;top:146px;width:283px;height:343px;background:#fff;box-shadow:0 2px 9px rgba(0,0,0,.16);border-bottom:3px solid var(--gold);text-align:center}
.service .photo{position:absolute;left:6px;top:6px;width:271px;height:180px}
.card-title{font-family:var(--head);font-weight:700;font-size:12px;letter-spacing:1.5px;color:var(--ink);text-transform:uppercase;word-spacing:6px}
.service .card-title{position:absolute;left:0;right:0;top:212px}
.service p{position:absolute;left:22px;right:22px;top:240px;font-size:11px;line-height:20px}
/* team */
.member{position:absolute;top:160px;width:216px;height:318px;background:#fff;border:3px solid var(--gold);box-shadow:0 2px 9px rgba(0,0,0,.14);text-align:center}
.member.dark{border-color:var(--gray)}
.avatar{position:absolute;left:58px;top:30px;width:97px;height:97px;border-radius:50%}
.member .card-title{position:absolute;left:0;right:0;top:160px;font-size:13px}
.member .rule{position:absolute;left:91px;top:183px;width:32px;height:2px;background:var(--gold)}
.member p{position:absolute;left:12px;right:12px;top:195px;font-size:11px;line-height:19px}
/* workflow */
.step{position:absolute;top:256px;width:168px;height:182px;background:#fff;box-shadow:0 2px 8px rgba(0,0,0,.10);border-top:3px solid var(--ink);text-align:center}
.step.gold{border-top-color:var(--gold)}
.diamond{position:absolute;left:50%;top:-38px;width:54px;height:54px;margin-left:-27px;transform:rotate(45deg);background:linear-gradient(135deg,#5a5a5e,var(--ink-dark))}
.step.gold .diamond{background:linear-gradient(135deg,var(--gold-light),var(--gold))}
.diamond svg{position:absolute;left:13px;top:13px;transform:rotate(-45deg)}
.step .card-title{position:absolute;left:0;right:0;top:52px;font-size:11.5px}
.step p{position:absolute;left:10px;right:10px;top:78px;font-size:10px;line-height:19px}
/* chart */
.info{position:absolute;left:678px;top:132px;width:310px;height:371px;background:linear-gradient(180deg,#3c3c40,#77777b)}
.info-item{position:absolute;left:0;width:310px;height:110px}
.info-item .gem{position:absolute;left:26px;top:36px;width:46px;height:46px;transform:rotate(45deg);background:linear-gradient(135deg,var(--gold-light),var(--gold))}
.info-item h4{position:absolute;left:103px;top:20px;font-family:var(--head);font-size:12px;letter-spacing:1.5px;color:#fff;font-weight:700}
.info-item p{position:absolute;left:103px;top:40px;width:190px;font-size:9px;line-height:13px;color:#e8e8e8;text-align:justify}
/* price */
.plan{position:absolute;top:132px;width:247px;height:390px;background:linear-gradient(180deg,#3a3a3e,#76767a);box-shadow:0 3px 10px rgba(0,0,0,.2);border:2px solid #fff;outline:1px solid #ddd;color:#fff;text-align:center}
.plan.gold{background:linear-gradient(180deg,#c38a34,#ecca66)}
.plan h3{position:absolute;left:0;right:0;top:28px;font-family:var(--head);font-size:18px;letter-spacing:1.5px;font-weight:700}
.plan .price{position:absolute;left:0;right:0;top:64px;font-size:28px;font-weight:700;color:var(--gold-light)}
.plan.gold .price{color:#fff}
.plan .divider{position:absolute;left:18px;right:18px;top:116px;height:1px;background:rgba(255,255,255,.3)}
.plan h5{position:absolute;left:0;right:0;top:132px;font-size:13px;font-weight:700}
.plan ul{position:absolute;left:28px;right:16px;top:162px;list-style:none;text-align:left}
.plan li{position:relative;padding-left:20px;font-size:10.5px;line-height:15px;margin-bottom:11px;color:#f2f2f2}
.plan li::before{content:"";position:absolute;left:0;top:3px;width:9px;height:9px;border-radius:50%;background:var(--gold-light)}
.plan.gold li::before{background:var(--ink)}
</style>
</head>
<body>

<!-- Teaser -->
<section class="slide" style="top:88px">
  <svg class="abs" style="left:0;top:0" width="1048" height="588" viewBox="0 0 1048 588">
    <defs>
      <linearGradient id="tzDark" x1="0" y1="0" x2="0" y2="1"><stop offset="0" stop-color="#3a3a3e"/><stop offset="1" stop-color="#6c6c70"/></linearGradient>
      <linearGradient id="tzGold" x1="0" y1="0" x2="0" y2="1"><stop offset="0" stop-color="#9c6c2a"/><stop offset="1" stop-color="#d7a349"/></linearGradient>
      <linearGradient id="tzPhoto" x1="0" y1="0" x2="1" y2="1"><stop offset="0" stop-color="#b7aa99"/><stop offset=".5" stop-color="#7d6d5f"/><stop offset="1" stop-color="#d8d2c8"/></linearGradient>
    </defs>
    <rect x="360" y="0" width="688" height="588" fill="url(#tzPhoto)" role="img" aria-label="Photo of two builders reviewing construction plans at a drafting table"/>
    <polygon points="0,0 370,0 612,588 0,588" fill="url(#tzDark)"/>
    <polygon points="466,234 370,588 612,588" fill="url(#tzGold)"/>
  </svg>
  <div class="logo light" style="left:61px;top:44px"><span class="logo-mark"></span><div class="logo-name">Nivel Crest</div></div>
  <h1 class="abs teaser-title">TEASER</h1>
  <div class="abs teaser-rule"></div>
  <p class="abs teaser-copy">Lorem ipsum dolor sit amet, consectetur adipiscing elit, sed do eiusmod tempor incididunt ut labore et dolore magna aliqua. Ut enim ad minim veniam, quis nostrud exercitation ullamco laboris nisi ut aliquip ex ea commodo consequat duis aute irure dolor in reprehenderit in voluptate velit esse cillum.</p>
</section>

<!-- Services -->
<section class="slide" style="top:738px">
  <svg class="band" width="1048" height="32"><polygon points="0,0 790,0 770,20 0,20" fill="#3a3a3e"/><polyline points="725,30 768,4 1048,4" fill="none" stroke="#c38a34" stroke-width="3"/></svg>
  <div class="logo" style="left:790px;top:26px"><span class="logo-mark"></span><div class="logo-name">Nivel Crest</div></div>
  <h2 class="title"><span class="accent">Our</span> Services</h2>
  <article class="service" style="left:61px"><div class="photo" role="img" aria-label="Photo of two consultants reviewing documents in an office" style="background:linear-gradient(135deg,#d9dde0,#8e959b)"></div><h3 class="card-title">Lorem ipsum dol</h3><p>Lorem ipsum dolor sit amet, consectetur adipiscing elit, sed do eiusmod tempor incididunt ut labore et dolore magna aliqua ut enim ad minim veniam, quis nostrud exercitea.</p></article>
  <article class="service" style="left:381px"><div class="photo" role="img" aria-label="Photo of a small house model and keys on a desk" style="background:linear-gradient(135deg,#6f6660,#2f2b29)"></div><h3 class="card-title">Lorem ipsum dol</h3><p>Lorem ipsum dolor sit amet, consectetur adipiscing elit, sed do eiusmod tempor incididunt ut labore et dolore magna aliqua ut enim ad minim veniam, quis nostrud exercitea.</p></article>
  <article class="service" style="left:703px"><div class="photo" role="img" aria-label="Photo of engineers in hard hats on a construction site" style="background:linear-gradient(135deg,#d9a45a,#7b5e4d)"></div><h3 class="card-title">Lorem ipsum dol</h3><p>Lorem ipsum dolor sit amet, consectetur adipiscing elit, sed do eiusmod tempor incididunt ut labore et dolore magna aliqua ut enim ad minim veniam, quis nostrud exercitea.</p></article>
</section>

<!-- Team -->
<section class="slide" style="top:1397px">
  <svg class="band" width="1048" height="32"><polygon points="0,0 790,0 770,20 0,20" fill="#3a3a3e"/><polyline points="725,30 768,4 1048,4" fill="none" stroke="#c38a34" stroke-width="3"/></svg>
  <div class="logo" style="left:790px;top:26px"><span class="logo-mark"></span><div class="logo-name">Nivel Crest</div></div>
  <h2 class="title"><span class="accent">Our</span> Team</h2>
  <article class="member" style="left:61px"><div class="avatar" role="img" aria-label="Portrait photo of team member" style="background:radial-gradient(circle at 50% 40%,#c9b3a3,#7b7b7b)"></div><h3 class="card-title">John Smith</h3><div class="rule"></div><p>Lorem ipsum dolor sit amet, consectetur adipiscing elit, sed do eiusmod tempor incididunt ut labore et dolore magna aliqua ut enim ad minim lorum veniam.</p></article>
  <article class="member dark" style="left:297px"><div class="avatar" role="img" aria-label="Portrait photo of team member" style="background:radial-gradient(circle at 50% 40%,#d8b49a,#9a7a66)"></div><h3 class="card-title">John Smith</h3><div class="rule"></div><p>Lorem ipsum dolor sit amet, consectetur adipiscing elit, sed do eiusmod tempor incididunt ut labore et dolore magna aliqua ut enim ad minim lorum veniam.</p></article>
  <article class="member" style="left:533px"><div class="avatar" role="img" aria-label="Portrait photo of team member" style="background:radial-gradient(circle at 50% 40%,#b59a88,#4a4a4e)"></div><h3 class="card-title">John Smith</h3><div class="rule"></div><p>Lorem ipsum dolor sit amet, consectetur adipiscing elit, sed do eiusmod tempor incididunt ut labore et dolore magna aliqua ut enim ad minim lorum veniam.</p></article>
  <article class="member dark" style="left:770px"><div class="avatar" role="img" aria-label="Portrait photo of team member" style="background:radial-gradient(circle at 50% 40%,#f0d2bb,#c9a06e)"></div><h3 class="card-title">John Smith</h3><div class="rule"></div><p>Lorem ipsum dolor sit amet, consectetur adipiscing elit, sed do eiusmod tempor incididunt ut labore et dolore magna aliqua ut enim ad minim lorum veniam.</p></article>
</section>

<!-- Workflows -->
<section class="slide" style="top:2056px">
  <svg class="band" width="1048" height="32"><polygon points="0,0 790,0 770,20 0,20" fill="#3a3a3e"/><polyline points="725,30 768,4 1048,4" fill="none" stroke="#c38a34" stroke-width="3"/></svg>
  <div class="logo" style="left:790px;top:26px"><span class="logo-mark"></span><div class="logo-name">Nivel Crest</div></div>
  <h2 class="title"><span class="accent">Capacities and</span> Present Workflows</h2>
  <svg class="abs" style="left:0;top:0" width="1048" height="588" fill="none" stroke="#dcdcdc" stroke-width="7" stroke-linecap="round">
    <path d="M350 185 Q430 135 500 170"/><polygon points="490,152 516,180 486,186" fill="#dcdcdc" stroke="none"/>
    <path d="M725 185 Q805 135 875 170"/><polygon points="865,152 891,180 861,186" fill="#dcdcdc" stroke="none"/>
    <path d="M160 498 Q240 530 310 478"/><polygon points="298,470 320,468 312,490" fill="#dcdcdc" stroke="none"/>
    <path d="M535 498 Q615 530 685 478"/><polygon points="673,470 695,468 687,490" fill="#dcdcdc" stroke="none"/>
  </svg>
  <div class="step" style="left:61px"><div class="diamond"><svg width="28" height="28" viewBox="0 0 28 28" fill="none" stroke="#fff" stroke-width="1.6"><rect x="4" y="10" width="20" height="14"/><path d="M8 10V5h6v5M4 17h20"/></svg></div><h3 class="card-title">Lorem ipsum</h3><p>Lorem ipsum dolor sit amet, consectetur adip iscing elit, sed do eiusmod tempor incididunt ut labore et dolore.</p></div>
  <div class="step gold" style="left:251px"><div class="diamond"><svg width="28" height="28" viewBox="0 0 28 28" fill="none" stroke="#fff" stroke-width="1.6"><rect x="6" y="8" width="9" height="16"/><rect x="15" y="13" width="8" height="11"/><path d="M3 24h22"/></svg></div><h3 class="card-title">Lorem ipsum</h3><p>Lorem ipsum dolor sit amet, consectetur adip iscing elit, sed do eiusmod tempor incididunt ut labore et dolore.</p></div>
  <div class="step" style="left:440px"><div class="diamond"><svg width="28" height="28" viewBox="0 0 28 28" fill="none" stroke="#fff" stroke-width="1.6"><rect x="4" y="6" width="20" height="16" rx="2"/><circle cx="14" cy="14" r="4"/></svg></div><h3 class="card-title">Lorem ipsum</h3><p>Lorem ipsum dolor sit amet, consectetur adip iscing elit, sed do eiusmod tempor incididunt ut labore et dolore.</p></div>
  <div class="step gold" style="left:630px"><div class="diamond"><svg width="28" height="28" viewBox="0 0 28 28" fill="none" stroke="#fff" stroke-width="1.6"><circle cx="14" cy="14" r="9"/><path d="M14 9v10M11 12h5M11 16h5"/></svg></div><h3 class="card-title">Lorem ipsum</h3><p>Lorem ipsum dolor sit amet, consectetur adip iscing elit, sed do eiusmod tempor incididunt ut labore et dolore.</p></div>
  <div class="step" style="left:819px"><div class="diamond"><svg width="28" height="28" viewBox="0 0 28 28" fill="none" stroke="#fff" stroke-width="1.6"><circle cx="14" cy="14" r="5"/><path d="M14 4v4M14 20v4M4 14h4M20 14h4M7 7l3 3M18 18l3 3M21 7l-3 3M10 18l-3 3"/></svg></div><h3 class="card-title">Lorem ipsum</h3><p>Lorem ipsum dolor sit amet, consectetur adip iscing elit, sed do eiusmod tempor incididunt ut labore et dolore.</p></div>
</section>

<!-- Organization charts -->
<section class="slide" style="top:2714px">
  <svg class="band" width="1048" height="32"><polygon points="0,0 790,0 770,20 0,20" fill="#3a3a3e"/><polyline points="725,30 768,4 1048,4" fill="none" stroke="#c38a34" stroke-width="3"/></svg>
  <div class="logo" style="left:790px;top:26px"><span class="logo-mark"></span><div class="logo-name">Nivel Crest</div></div>
  <h2 class="title"><span class="accent">Organization</span> Charts</h2>
  <svg class="abs" style="left:0;top:0" width="670" height="588" viewBox="0 0 670 588" font-family="Open Sans, sans-serif" font-size="12" font-weight="600" fill="#3a3a3e">
    <defs>
      <linearGradient id="barDark" x1="0" y1="0" x2="0" y2="1"><stop offset="0" stop-color="#38383c"/><stop offset="1" stop-color="#8a8a8e"/></linearGradient>
      <linearGradient id="barGold" x1="0" y1="0" x2="0" y2="1"><stop offset="0" stop-color="#e8c25e"/><stop offset="1" stop-color="#b07a2c"/></linearGradient>
    </defs>
    <g stroke="#e6e6e6" stroke-width="1">
      <line x1="90" y1="135" x2="651" y2="135"/><line x1="90" y1="193" x2="651" y2="193"/><line x1="90" y1="250" x2="651" y2="250"/><line x1="90" y1="308" x2="651" y2="308"/><line x1="90" y1="366" x2="651" y2="366"/><line x1="90" y1="423" x2="651" y2="423"/><line x1="90" y1="481" x2="651" y2="481"/>
      <line x1="90" y1="135" x2="90" y2="481"/><line x1="170" y1="135" x2="170" y2="481"/><line x1="250" y1="135" x2="250" y2="481"/><line x1="330" y1="135" x2="330" y2="481"/><line x1="410" y1="135" x2="410" y2="481"/><line x1="490" y1="135" x2="490" y2="481"/><line x1="570" y1="135" x2="570" y2="481"/><line x1="651" y1="135" x2="651" y2="481"/>
    </g>
    <g text-anchor="end"><text x="82" y="139">120</text><text x="82" y="197">100</text><text x="82" y="254">80</text><text x="82" y="312">60</text><text x="82" y="370">40</text><text x="82" y="427">20</text><text x="82" y="485">0</text></g>
    <g fill="url(#barDark)">
      <rect x="113" y="193" width="15" height="288"/><rect x="193" y="222" width="15" height="259"/><rect x="273" y="337" width="15" height="144"/><rect x="353" y="193" width="15" height="288"/><rect x="433" y="193" width="15" height="288"/><rect x="513" y="308" width="15" height="173"/><rect x="593" y="337" width="15" height="144"/>
    </g>
    <g fill="url(#barGold)">
      <rect x="133" y="222" width="15" height="259"/><rect x="213" y="250" width="15" height="231"/><rect x="293" y="193" width="15" height="288"/><rect x="373" y="308" width="15" height="173"/><rect x="453" y="222" width="15" height="259"/><rect x="533" y="265" width="15" height="216"/><rect x="613" y="193" width="15" height="288"/>
    </g>
    <g text-anchor="middle" font-size="11.5">
      <text x="120" y="187">100</text><text x="141" y="216">90</text>
      <text x="200" y="216">90</text><text x="221" y="244">80</text>
      <text x="280" y="331">50</text><text x="301" y="187">100</text>
      <text x="360" y="187">100</text><text x="381" y="302">60</text>
      <text x="440" y="187">100</text><text x="461" y="216">90</text>
      <text x="520" y="302">60</text><text x="541" y="259">75</text>
      <text x="600" y="331">50</text><text x="621" y="187">100</text>
    </g>
    <g text-anchor="middle"><text x="130" y="502">Sun</text><text x="210" y="502">Mon</text><text x="290" y="502">Tue</text><text x="370" y="502">Wed</text><text x="450" y="502">Thu</text><text x="530" y="502">Fri</text><text x="610" y="502">Sat</text></g>
  </svg>
  <aside class="info">
    <div class="info-item" style="top:10px"><span class="gem"></span><h4>LORUM IPSUM</h4><p>Lorem ipsum dolor sit amet, consectetur adipiscing elit, sed do eiusmod tempor incididunt ut labore et dolore magna aliqua. Ut enim ad minim veniam, quis nostrud exercitation ullamco.</p></div>
    <div class="info-item" style="top:122px"><span class="gem"></span><h4>LORUM IPSUM</h4><p>Lorem ipsum dolor sit amet, consectetur adipiscing elit, sed do eiusmod tempor incididunt ut labore et dolore magna aliqua. Ut enim ad minim veniam, quis nostrud exercitation ullamco.</p></div>
    <div class="info-item" style="top:234px"><span class="gem"></span><h4>LORUM IPSUM</h4><p>Lorem ipsum dolor sit amet, consectetur adipiscing elit, sed do eiusmod tempor incididunt ut labore et dolore magna aliqua. Ut enim ad minim veniam, quis nostrud exercitation ullamco.</p></div>
  </aside>
</section>

<!-- Price lists -->
<section class="slide" style="top:3373px">
  <svg class="band" width="1048" height="32"><polygon points="0,0 790,0 770,20 0,20" fill="#3a3a3e"/><polyline points="725,30 768,4 1048,4" fill="none" stroke="#c38a34" stroke-width="3"/></svg>
  <div class="logo" style="left:790px;top:26px"><span class="logo-mark"></span><div class="logo-name">Nivel Crest</div></div>
  <h2 class="title"><span class="accent">Price</span> Lists</h2>
  <article class="plan" style="left:120px"><h3>MONTHLY</h3><div class="price">$250</div><div class="divider"></div><h5>Features</h5>
    <ul><li>Lorem ipsum dolor sit amet, cons ectetur adipisea</li><li>Sed ut perspiciatis unde omnis is tenatus error</li><li>Lorem ipsum dolor sit amet</li><li>Sed ut perspiciatis unde omnis</li><li>Lorem ipsum dolor sit amet, cons ectetur adipisea</li><li>Lorem ipsum dolor sit amet</li></ul></article>
  <article class="plan gold" style="left:402px"><h3>ANNUAL</h3><div class="price">$250</div><div class="divider"></div><h5>Features</h5>
    <ul><li>Lorem ipsum dolor sit amet, cons ectetur adipisea</li><li>Sed ut perspiciatis unde omnis is tenatus error</li><li>Lorem ipsum dolor sit amet</li><li>Sed ut perspiciatis unde omnis</li><li>Lorem ipsum dolor sit amet, cons ectetur adipisea</li><li>Lorem ipsum dolor sit amet</li></ul></article>
  <article class="plan" style="left:683px"><h3>FOREVER</h3><div class="price">$250</div><div class="divider"></div><h5>Features</h5>
    <ul><li>Lorem ipsum dolor sit amet, cons ectetur adipisea</li><li>Sed ut perspiciatis unde omnis is tenatus error</li><li>Lorem ipsum dolor sit amet</li><li>Sed ut perspiciatis unde omnis</li><li>Lorem ipsum dolor sit amet, cons ectetur adipisea</li><li>Lorem ipsum dolor sit amet</li></ul></article>
</section>

</body>
</html>
```